Business Card Design Project

Business Card
We are rebranding with a new logo
Industry/Entity Type
Business
Contact Information for Business Card
Dennis Morvale +61 487215963 dennis@quorv.com.au P.O. Box 872 Fernlow QLD 4309
Requirements
Must have
- Logo

```html
<!DOCTYPE html>
<html lang="en">
<head>
<meta charset="utf-8">
<title>Quorv International — Business Card</title>
<link href="https://fonts.googleapis.com/css2?family=Questrial&display=swap" rel="stylesheet">
<style>
  :root {
    --backdrop: #dfe3e8;
    --card-light: #f4f6f8;
    --navy: #1c3850;
    --band-orange: #e8581a;
    --band-red: #c9361a;
    --band-blue: #1f5c9e;
    --text-white: #ffffff;
    --text-lavender: #b9b9e6;
    --text-muted: #9c9cd0;
    --brand-ink: #25435f;
  }
  * { margin: 0; padding: 0; box-sizing: border-box; }
  html, body {
    width: 1200px; height: 899px; overflow: hidden;
    background: var(--backdrop);
    font-family: "Questrial", "Century Gothic", sans-serif;
  }
  .card {
    position: absolute; left: 100px; top: 164px;
    width: 1000px; height: 571px;
    background: var(--card-light);
    overflow: hidden;
    box-shadow: 0 10px 30px rgba(20, 40, 60, 0.18);
  }
  .card-art { position: absolute; inset: 0; width: 100%; height: 100%; }
  .brand {
    position: absolute; left: 70px; top: 220px; width: 430px;
    text-align: center; color: var(--brand-ink);
  }
  .brand-name { font-size: 92px; line-height: 1; letter-spacing: 2px; }
  .brand-sub { font-size: 34px; letter-spacing: 6px; margin-top: 14px; }
  .holder {
    position: absolute; right: 62px; top: 150px;
    font-size: 29px; color: var(--text-white); letter-spacing: 0.5px;
    text-transform: uppercase;
  }
  .contacts { position: absolute; right: 62px; top: 237px; list-style: none; }
  .contacts li {
    display: flex; justify-content: flex-end; align-items: center;
    height: 29px; font-size: 21px; letter-spacing: 0.5px;
    color: var(--text-lavender);
  }
  .contacts li.phone { color: var(--text-white); }
  .contacts svg { width: 20px; height: 20px; margin-left: 14px; flex: none; }
  .address {
    position: absolute; right: 62px; top: 367px;
    text-align: right; font-size: 21px; line-height: 29px;
    color: var(--text-muted); letter-spacing: 0.5px;
  }
</style>
</head>
<body>
<div class="card">
  <svg class="card-art" viewBox="0 0 936 534" preserveAspectRatio="none" aria-hidden="true">
    <path fill="var(--band-orange)" d="M440 0 C520 120 520 360 355 534 L936 534 L936 0 Z"/>
    <path fill="var(--band-red)" d="M482 0 C552 120 542 370 378 534 L936 534 L936 0 Z"/>
    <path fill="var(--band-blue)" d="M508 0 C570 125 556 385 396 534 L936 534 L936 0 Z"/>
    <path fill="var(--navy)" d="M525 0 C582 132 562 392 424 534 L936 534 L936 0 Z"/>
  </svg>

  <div class="brand">
    <div class="brand-name">Quorv</div>
    <div class="brand-sub">INTERNATIONAL</div>
  </div>

  <div class="holder">Dennis Morvale</div>

  <ul class="contacts">
    <li class="phone">+61 487215963
      <svg viewBox="0 0 24 24"><path fill="currentColor" d="M6.6 10.8a15.2 15.2 0 0 0 6.6 6.6l2.2-2.2a1 1 0 0 1 1-.25 11.4 11.4 0 0 0 3.6.57 1 1 0 0 1 1 1V20a1 1 0 0 1-1 1A17 17 0 0 1 3 4a1 1 0 0 1 1-1h3.5a1 1 0 0 1 1 1c0 1.25.2 2.45.57 3.57a1 1 0 0 1-.25 1z"/></svg>
    </li>
    <li class="email">dennis@quorv.com.au
      <svg viewBox="0 0 24 24"><rect x="2" y="5" width="20" height="14" fill="currentColor"/><path d="M2 5 L12 13 L22 5 M2 19 L9 11 M22 19 L15 11" stroke="var(--navy)" stroke-width="1.8" fill="none"/></svg>
    </li>
    <li class="web">www.quorv.com.au
      <svg viewBox="0 0 24 24" fill="none" stroke="currentColor" stroke-width="1.6"><circle cx="12" cy="12" r="9.5"/><ellipse cx="12" cy="12" rx="4.2" ry="9.5"/><path d="M2.5 12h19M4 7h16M4 17h16"/></svg>
    </li>
  </ul>

  <div class="address">
    P.O. Box 872 Fernlow<br>QLD 4309
  </div>
</div>
</body>
</html>
```